New career and executive coaching business needs a business card design including logo

Company name: 'Bramblefield Growth Partners.' The aim of my coaching engagements is to help people improve their communication in the workplace and achieve their career goals. The process involves working with individuals to help them uncover their strengths and talents, then leverage those to improve their working lives. The Tarwick Inventory is the starting point to the process. I am after an exciting and interesting business card design (including logo)which is professional yet will still get people's attention.

Industry/Entity Type

Business

Contact Information for Business Card

Name: Malcolm Dervaney
Position: Owner
Address: 58 Quorrin Ct, Elmbridge Vic 3190
Phone: 0418923047
Website: bramblefieldgrowth.com.au
Email: malcolm@bgp.com.au

Colors
33a6d7
00a990
0355a3
3176b5

Requirements
Must have
• logo

```html
<!DOCTYPE html>
<html lang="en">
<head>
<meta charset="utf-8">
<title>Bramblefield Growth Partners – Business Card</title>
<link rel="stylesheet" href="https://fonts.googleapis.com/css2?family=Open+Sans:wght@400;600;700&display=swap">
<style>
  :root {
    --stage-top: #2a2a2a;
    --stage-bottom: #050505;
    --card-front: #f3f3f3;
    --ink: #111111;
    --ink-soft: #333333;
    --brand-blue: #1a6fbb;
    --brand-sky: #33a6d7;
    --brand-navy: #0355a3;
    --back-light: #2f8fd0;
    --back-mid: #1769b6;
    --back-dark: #0652a2;
    --back-glow: rgba(255, 255, 255, 0.08);
    --white: #ffffff;
  }
  * { margin: 0; padding: 0; box-sizing: border-box; }
  html, body { width: 1200px; height: 900px; overflow: hidden; }
  body {
    position: relative;
    background: linear-gradient(180deg, var(--stage-top) 0%, #151515 60%, var(--stage-bottom) 100%);
    font-family: "Open Sans", Arial, sans-serif;
  }
  .card {
    position: absolute;
    top: 184px;
    height: 490px;
    border-radius: 12px;
    box-shadow: 0 4px 14px rgba(0, 0, 0, 0.55);
    overflow: hidden;
  }
  .card-front {
    left: 299px;
    width: 301px;
    background: var(--card-front);
    text-align: center;
  }
  .card-back {
    left: 645px;
    width: 304px;
    background: radial-gradient(ellipse at 50% 42%, var(--back-light) 0%, var(--back-mid) 45%, var(--back-dark) 100%);
  }
  .brand-mark {
    position: absolute;
    left: 50%;
    top: 34px;
    transform: translateX(-50%);
    width: 122px;
    height: 122px;
    border-radius: 50%;
    background: linear-gradient(135deg, var(--brand-sky), var(--brand-navy));
  }
  .back-mark {
    position: absolute;
    left: 50%;
    top: 62px;
    transform: translateX(-50%);
    width: 300px;
    height: 300px;
    border-radius: 50%;
    background: var(--back-glow);
  }
  .brand-name {
    position: absolute;
    left: 0;
    right: 0;
    text-align: center;
    font-weight: 700;
    font-size: 23px;
    line-height: 27px;
    letter-spacing: 0.2px;
  }
  .card-front .brand-name { top: 178px; color: var(--ink); }
  .card-back .brand-name { top: 378px; color: var(--white); }
  .holder-name {
    position: absolute;
    left: 0; right: 0;
    top: 268px;
    font-size: 18px;
    font-weight: 600;
    line-height: 24px;
    color: var(--brand-blue);
    letter-spacing: 0.3px;
  }
  .holder-role {
    position: absolute;
    left: 0; right: 0;
    top: 293px;
    font-size: 14px;
    line-height: 18px;
    color: var(--ink-soft);
  }
  .contact-list {
    position: absolute;
    left: 0; right: 0;
    top: 341px;
    list-style: none;
    font-size: 14px;
    line-height: 20px;
    color: var(--ink-soft);
  }
  .contact-list li { display: flex; justify-content: center; align-items: center; gap: 8px; }
  .contact-list svg { width: 10px; height: 10px; fill: var(--brand-blue); flex: none; }
  .address {
    position: absolute;
    left: 0; right: 0;
    top: 420px;
    font-size: 14px;
    line-height: 17px;
    color: var(--ink-soft);
    font-style: normal;
  }
</style>
</head>
<body>
  <section class="card card-front" aria-label="Card front">
    <div class="brand-mark" aria-hidden="true"></div>
    <div class="brand-name">Bramblefield<br>Growth Partners</div>
    <h1 class="holder-name">MALCOLM DERVANEY</h1>
    <p class="holder-role">Owner</p>
    <ul class="contact-list">
      <li>
        <svg viewBox="0 0 10 10" aria-hidden="true"><path d="M1 3.5C1 2 2.5 1 5 1s4 1 4 2.5L7.5 4.5 6.8 3.2H3.2L2.5 4.5zM2.5 5h5l1 4h-7z"/></svg>
        <span>0418923047</span>
      </li>
      <li>
        <svg viewBox="0 0 10 10" aria-hidden="true"><path d="M0 2h10v6H0zM0.6 2.4 5 5.6l4.4-3.2" stroke="#f3f3f3" stroke-width="0.8"/></svg>
        <span>malcolm@bgp.com.au</span>
      </li>
      <li>
        <svg viewBox="0 0 10 10" aria-hidden="true"><circle cx="5" cy="5" r="4.2" fill="none" stroke="#1a6fbb" stroke-width="1"/><path d="M0.8 5h8.4M5 0.8c-2.2 2.4-2.2 6 0 8.4M5 0.8c2.2 2.4 2.2 6 0 8.4" fill="none" stroke="#1a6fbb" stroke-width="0.8"/></svg>
        <span>bramblefieldgrowth.com.au</span>
      </li>
    </ul>
    <address class="address">58 Quorrin Ct<br>Elmbridge Vic 3190</address>
  </section>

  <section class="card card-back" aria-label="Card back">
    <div class="back-mark" aria-hidden="true"></div>
    <div class="brand-name">Bramblefield<br>Growth Partners</div>
  </section>
</body>
</html>
```